To design a look and feel for a website. The company offers technical services to governemtns and public bodies. It does NOT market to the public.

The core business is GIS (Geographic Information Systems)

The site needs to be clean and simple, The current version is available here: www.velda-maps.ie

Thanks for your interest in our project

Target Market(s)

Goverment agencies and public bodies in the EU, buying through the public procurerment process

Requirements
Should not have
• corny graphics of hands holding globes or sateliites please.

```html
<!DOCTYPE html>
<html lang="en">
<head>
<meta charset="utf-8">
<title>The VELDA Group – Information Expertise</title>
<link href="https://fonts.googleapis.com/css2?family=Oswald:wght@400;500&family=Oxygen:wght@400;700&display=swap" rel="stylesheet">
<style>
:root{
  --navy:#22408a;
  --navy-dark:#1b2f6b;
  --footer:#243a7f;
  --lilac:#7d75bc;
  --lilac-text:#7a72b8;
  --ink:#555a63;
  --page:#f5f5f5;
  --line:#d6d6d6;
  --white:#ffffff;
}
*{margin:0;padding:0;box-sizing:border-box}
html,body{width:927px;height:1200px;overflow:hidden;background:var(--page)}
body{font-family:'Oxygen',sans-serif;color:var(--ink)}
.page{position:relative;width:927px;height:1200px;overflow:hidden;background:var(--page)}
.abs{position:absolute}

.header{left:0;top:0;width:927px;height:94px;background:linear-gradient(#f3f3f3,#fdfdfd);border-top:3px solid var(--lilac)}
.brand{left:105px;top:22px;display:flex;align-items:center;gap:6px}
.brand-dot{width:10px;height:10px;border-radius:50%;background:var(--lilac)}
.brand-name{font-family:'Oswald',sans-serif;font-size:25px;font-weight:500;color:var(--navy);line-height:1}
.tagline{left:106px;top:76px;font-size:10px;color:var(--lilac-text)}
.phone-tab{left:680px;top:0;width:142px;height:29px;background:var(--lilac);border-radius:0 0 10px 10px;display:flex;align-items:center;justify-content:center;gap:7px;color:var(--white);font-family:'Oswald',sans-serif;font-size:16px}

.nav{left:0;top:94px;width:927px;height:30px;background:linear-gradient(var(--navy),var(--navy-dark));display:flex;padding-left:101px}
.nav a{color:var(--white);text-decoration:none;font-size:13px;line-height:30px;padding:0 13px;border-right:1px solid #14245a}
.nav a.active{background:#3a4f94;width:83px;text-align:center}

.hero{left:0;top:124px;width:927px;height:378px;background:linear-gradient(135deg,#8a8f94 0%,#c8cbc9 30%,#a8c476 50%,#c1c4c6 70%,#7d8288 100%)}
.caption{left:0;top:456px;width:927px;height:46px;background:rgba(20,30,70,.78)}
.caption p{position:absolute;left:106px;top:4px;width:580px;color:var(--white);font-weight:700;font-size:14px;line-height:19px}
.dots{left:720px;top:472px;display:flex;gap:7px}
.dots span{width:15px;height:15px;border-radius:50%;background:var(--lilac)}
.dots span.on{background:var(--white)}

.tab{width:111px;height:28px;background:linear-gradient(#5e5aa0,#34336f);color:var(--white);font-size:13px;font-weight:700;text-align:center;line-height:28px;border-radius:0 0 5px 5px;left:408px}

.service{width:140px;text-align:center}
.service svg{display:block;margin:0 auto}
.service span{display:block;margin-top:7px;font-size:13.5px;color:var(--lilac-text)}
.rule{left:101px;top:661px;width:726px;height:1px;background:var(--line)}

.about{left:115px;top:678px;width:473px}
.about h2{font-family:'Oswald',sans-serif;font-weight:400;color:var(--navy);font-size:19px;line-height:26px;margin-bottom:6px}
.about p{font-size:9.3px;line-height:12.8px;margin-bottom:9px}

.news{left:616px;top:676px;width:196px;height:227px;border:1px solid #c9c9c9;border-radius:4px;background:#f1f1f1;padding:3px 10px;box-shadow:0 2px 2px #d0d0d0;overflow:hidden}
.news h2{font-family:'Oswald',sans-serif;font-weight:400;color:var(--navy);font-size:19px;line-height:24px;border-bottom:1px solid #ccc;padding-bottom:4px;margin-bottom:9px}
.item{display:flex;gap:6px;height:45px}
.item.last{height:30px}
.date{width:20px;height:23px;flex:none;background:#d7d7d7;font-size:7px;text-align:center;line-height:10px;color:var(--navy)}
.date b{display:block;background:#8f8f8f;color:#fff}
.item p{font-size:9px;line-height:12.8px}
.item strong{color:#555}
.more{display:block;font-family:'Oswald',sans-serif;font-size:11px;line-height:14px;color:var(--navy)}

.clients-line{left:120px;top:930px;width:687px;height:2px;background:radial-gradient(#cfcfcf,transparent 70%)}
.arrow{width:28px;height:28px;border:2px solid #c9c9c9;border-radius:50%;top:968px}
.client{top:972px;height:24px;line-height:24px;white-space:nowrap;transform:translateX(-50%);font-size:12px;font-weight:700;color:var(--navy)}

.footer{left:0;top:1036px;width:927px;height:142px;background:var(--footer);color:var(--white)}
.footer h3{font-family:'Oswald',sans-serif;font-weight:400;font-size:13px;position:absolute;top:8px}
.links{position:absolute;left:117px;top:27px;list-style:none;font-size:10px}
.links li{display:block;height:22px;line-height:22px}
.links li::before{content:"▪ ";color:#8b90c0}
.map{position:absolute;left:214px;top:34px;width:98px;height:97px;background:linear-gradient(135deg,#e6e1d3,#d2ddc2 60%,#e9e6df)}
.contact{position:absolute;left:329px;font-size:10px;line-height:14px;display:flex;gap:10px}
.news-form p{position:absolute;left:492px;top:32px;width:170px;font-size:10px;line-height:15px}
.input{position:absolute;left:492px;top:77px;width:145px;height:22px;background:#fff;color:#888;font-size:9px;padding:5px 6px}
.submit{position:absolute;left:492px;top:109px;width:66px;height:21px;background:linear-gradient(#7873b6,#4e4a8d);font-size:9px;font-weight:700;text-align:center;line-height:21px;border-radius:2px}
.foot-brand{position:absolute;left:672px;top:40px;display:flex;align-items:center;gap:6px;font-family:'Oswald',sans-serif;font-size:24px;font-weight:500;color:#8d86cc}
.social{position:absolute;top:110px;display:flex;align-items:center;gap:3px;font-size:9px;font-weight:700}
.social i{width:10px;height:10px;background:#5aa0dc;display:block}
.copyright{left:0;top:1178px;width:927px;height:22px;background:var(--lilac);color:#fff;font-size:9.5px;text-align:center;line-height:22px}
</style>
</head>
<body>
<div class="page">

  <header class="header abs"></header>
  <div class="brand abs"><span class="brand-dot"></span><span class="brand-name">The VELDA Group</span></div>
  <div class="tagline abs">Information Expertise</div>
  <div class="phone-tab abs">
    <svg width="18" height="18" viewBox="0 0 18 18"><circle cx="9" cy="9" r="8" fill="none" stroke="#fff" stroke-width="1.6"/><path d="M11 4.5a5 5 0 0 0 0 9" fill="none" stroke="#fff" stroke-width="2"/></svg>
    353 1 555 0142
  </div>

  <nav class="nav abs">
    <a class="active" href="#">Home</a><a href="#">Services</a><a href="#">Clients</a><a href="#">Contact</a><a href="#" style="border:none">Inspire</a>
  </nav>

  <div class="hero abs" role="img" aria-label="Tablet showing a city map with location pins, standing among model city buildings"></div>
  <div class="caption abs"><p>... we can help with spatial vector data. VELDA also has a strong experise in general data management.</p></div>
  <div class="dots abs"><span class="on"></span><span></span><span></span><span></span></div>

  <div class="tab abs" style="top:497px">OUR SERVICES</div>

  <div class="service abs" style="left:92px;top:540px">
    <svg width="82" height="82" viewBox="0 0 82 82"><circle cx="41" cy="41" r="39" fill="#fff" stroke="#22408a" stroke-width="3"/><circle cx="41" cy="41" r="35" fill="#22408a"/><g stroke="#fff" stroke-width="4" stroke-linecap="round"><path d="M28 28l26 26M54 28L28 54"/></g><circle cx="28" cy="28" r="5" fill="none" stroke="#fff" stroke-width="2"/></svg>
    <span>Data Management</span></div>
  <div class="service abs" style="left:258px;top:540px">
    <svg width="82" height="82" viewBox="0 0 82 82"><circle cx="41" cy="41" r="39" fill="#fff" stroke="#22408a" stroke-width="3"/><circle cx="41" cy="41" r="35" fill="#22408a"/><circle cx="41" cy="41" r="17" fill="none" stroke="#fff" stroke-width="3"/><path d="M41 29l6 12-6 12-6-12z" fill="#fff"/></svg>
    <span>Spatial Data</span></div>
  <div class="service abs" style="left:404px;top:540px">
    <svg width="82" height="82" viewBox="0 0 82 82"><circle cx="41" cy="41" r="39" fill="#fff" stroke="#22408a" stroke-width="3"/><circle cx="41" cy="41" r="35" fill="#22408a"/><path d="M14 50l16-20 9 10 9-12 20 22z" fill="#fff"/></svg>
    <span>Land Use</span></div>
  <div class="service abs" style="left:550px;top:540px">
    <svg width="82" height="82" viewBox="0 0 82 82"><circle cx="41" cy="41" r="39" fill="#fff" stroke="#22408a" stroke-width="3"/><circle cx="41" cy="41" r="35" fill="#22408a"/><rect x="14" y="28" width="34" height="22" fill="#fff"/><path d="M50 34h10l6 8v8H50z" fill="#fff"/><circle cx="25" cy="53" r="5" fill="#fff" stroke="#22408a" stroke-width="2"/><circle cx="58" cy="53" r="5" fill="#fff" stroke="#22408a" stroke-width="2"/></svg>
    <span>Transport</span></div>
  <div class="service abs" style="left:697px;top:540px">
    <svg width="82" height="82" viewBox="0 0 82 82"><circle cx="41" cy="41" r="39" fill="#fff" stroke="#22408a" stroke-width="3"/><circle cx="41" cy="41" r="35" fill="#22408a"/><circle cx="41" cy="30" r="8" fill="#fff"/><path d="M26 58v-8a10 10 0 0 1 10-10h10a10 10 0 0 1 10 10v8z" fill="#fff"/></svg>
    <span>Consulting</span></div>

  <div class="rule abs"></div>

  <section class="about abs">
    <h2>About VELDA Group</h2>
    <p>The VELDA Group has been in business since 1994 and continues to develop and update its range of services. The company has a high level of expertise in handling data and information, and in building and re-engineering database systems. We have a particular expertise in working with Irish data sets and have a strong grounding in dealing with spatial data.</p>
    <p>We also have extensive experience in working in a Northwind development environment, both Desktop and WebForge. We have worked on development of small scale systems using Northwind products for over 12 years. We have assisted in the migration of systems from DeskBase to both DataCore Server and Quorra databases. This has included re-writing code from MacroScript to either ForgeBasic or ForgeSharp.</p>
    <p>We have built web sites for our clients using WebForge using Forge frameworks 1.5 through to 4.0. VELDA will work with all spatial data formats and systems including Quorra, GeoPlot/Xtend, Terrasys DataCore Server. We are not agents for any vendor, preferring to select the components that best suit the project's needs. The company's Quality Management System is ISO 9001:2008 certified (reviewed Jan 2012) The VELDA Group Ltd is registered in ireland number 401337</p>
  </section>

  <aside class="news abs">
    <h2>Latest News</h2>
    <div class="item"><div class="date"><b>DEC</b>21</div><p><strong>Lorem ipsum dolor sit amet,</strong> consectetuer adipiscing elit, sed diam nonummy nibh euismod cidunt</p></div>
    <div class="item"><div class="date"><b>DEC</b>21</div><p><strong>Lorem ipsum dolor sit amet,</strong> consectetuer adipiscing elit, sed diam nonummy nibh euismod cidunt</p></div>
    <div class="item"><div class="date"><b>DEC</b>21</div><p><strong>Lorem ipsum dolor sit amet,</strong> consectetuer adipiscing elit, sed diam nonummy</p></div>
    <div class="item last"><div class="date"><b>DEC</b>21</div><p><strong>Lorem ipsum dolor sit amet,</strong> consectetuer adipiscing elit, sed</p></div>
    <a class="more">View more</a>
  </aside>

  <div class="clients-line abs"></div>
  <div class="tab abs" style="top:927px">OUR CLIENTS</div>
  <div class="arrow abs" style="left:111px"><svg width="24" height="24" viewBox="0 0 24 24"><path d="M14 8l-5 4 5 4z" fill="#c9c9c9"/></svg></div>
  <div class="arrow abs" style="left:790px"><svg width="24" height="24" viewBox="0 0 24 24"><path d="M10 8l5 4-5 4z" fill="#c9c9c9"/></svg></div>
  <div class="client abs" style="left:208px">Roadlink</div>
  <div class="client abs" style="left:335px">Dept. of Lands</div>
  <div class="client abs" style="left:440px">Woodlands Board</div>
  <div class="client abs" style="left:525px">CareNet</div>
  <div class="client abs" style="left:619px">Eurodata</div>
  <div class="client abs" style="left:724px">Global Council</div>

  <footer class="footer abs">
    <h3 style="left:117px">Quick Links</h3>
    <ul class="links"><li>Home</li><li>Services</li><li>Clients</li><li>Contact</li><li>Inspire</li></ul>
    <h3 style="left:214px">Contact Info</h3>
    <div class="map" role="img" aria-label="Street map showing the office location"></div>
    <div class="contact" style="top:36px"><svg width="10" height="13" viewBox="0 0 10 13"><path d="M5 0a5 5 0 0 1 5 5c0 3-5 8-5 8S0 8 0 5a5 5 0 0 1 5-5z" fill="#8b90c0"/><circle cx="5" cy="5" r="2" fill="#243a7f"/></svg><span style="margin-left:4px">Lorem ipsum dolor<br>sit amet consectetuer,</span></div>
    <div class="contact" style="top:68px"><svg width="10" height="10" viewBox="0 0 10 10"><path d="M1 1h3l1 2-2 1a6 6 0 0 0 3 3l1-2 2 1v3C4 9 1 6 1 1z" fill="#8b90c0"/></svg><span style="margin-left:4px">+ 353 1 555 0142</span></div>
    <div class="contact" style="top:94px"><svg width="11" height="11" viewBox="0 0 11 11"><rect x="2" y="0" width="7" height="4" fill="#8b90c0"/><rect x="0" y="4" width="11" height="7" fill="#8b90c0"/></svg><span style="margin-left:4px">+ 353 1 555 0143</span></div>
    <div class="contact" style="top:118px"><svg width="11" height="8" viewBox="0 0 11 8"><rect width="11" height="8" fill="#8b90c0"/><path d="M0 0l5.5 4L11 0" stroke="#243a7f" fill="none"/></svg><span style="margin-left:4px">contact@velda-maps.ie</span></div>
    <h3 style="left:492px">Newsletter</h3>
    <div class="news-form"><p>Lorem ipsum dolor sit amet, consectetuer adipiscing elit, sed diam nonummy nibh</p></div>
    <div class="input">Enter your e-mail address</div>
    <div class="submit">SUBMIT</div>
    <div class="foot-brand"><span class="brand-dot"></span>The VELDA Group</div>
    <div class="social" style="left:684px"><i></i>Folio</div>
    <div class="social" style="left:726px"><i></i>Chirp</div>
    <div class="social" style="left:768px"><i></i>Netwk</div>
  </footer>
  <div class="copyright abs">© 2013 velda-maps.ie &nbsp;|&nbsp; All right reserved.</div>
</div>
</body>
</html>
```